Company or website name
- dalewintham.com
- Links to the website
- Vita Forge
- Describe your company and organization and target audience
- Founded by celebrity personal trainer and media personality Dale Wintham, Vita Forge provides high quality on-site fitness and wellness classes, and personal trainers for businesses and residential gyms throughout New York City. Our target audience are residents of high end buildings in NYC, that expect excellence and luxury
- The design should have the following
- This is a 24"x36" Poster for a complimentary event at a high end building. I would like the poster to look high end, luxury and simple and chique. The words should be clear and easy to read. It would be great to have a final copy that we can send to the printer and one which we can edit for future events Here is the text: The Halcott Spires Gym Complimentary Fitness & Wellness Event Complimentary Yoga, Pilates & Interval Training Bootcamp Classes PLUS: 30 Minute Private Training Sessions *Kids Karate Classes Also Available Saturday May 18th, 25th & June 1st Time: 9:00am - 12:15pm Halcott Spires Gym Schedule: 9:00am - 9:30am Yoga 9:45am - 10:15am Interval Training Bootcamp 11:45am -12:15pm Pilates 9:00am - 12:00pm Private Training Sessions Special Introductory Rate on Future Packages During Promotion www.Vitaforge.tv Info@vitaforge.tv
- Other Facts

```html
<!DOCTYPE html>
<html lang="en">
<head>
<meta charset="utf-8">
<title>Vita Forge – Complimentary Fitness &amp; Wellness Poster</title>
<link rel="stylesheet" href="https://fonts.googleapis.com/css2?family=Oswald:wght@400;500;600;700&family=Arimo:wght@400;700&display=swap">
<style>
  :root {
    --page: #ffffff;
    --charcoal: #2a2a2c;
    --charcoal-deep: #1b1b1d;
    --olive: #6f8f1f;
    --olive-dark: #4f6a14;
    --lime-link: #a6c83a;
    --blue-top: #2aa2f0;
    --blue-bottom: #0c5fb4;
    --white: #ffffff;
    --ghost: rgba(255, 255, 255, 0.07);
  }
  * { margin: 0; padding: 0; box-sizing: border-box; }
  html, body {
    width: 1200px;
    height: 960px;
    overflow: hidden;
    background: var(--page);
  }
  .poster {
    position: absolute;
    left: 295px;
    top: 21px;
    width: 610px;
    height: 918px;
    overflow: hidden;
    background: linear-gradient(160deg, var(--charcoal) 0%, var(--charcoal-deep) 100%);
    font-family: "Arimo", Arial, sans-serif;
    color: var(--white);
  }
  .brand-watermark {
    position: absolute;
    left: -330px;
    top: 520px;
    width: 760px;
    transform: rotate(-90deg);
    font-family: "Oswald", sans-serif;
    font-weight: 700;
    font-size: 92px;
    letter-spacing: 6px;
    color: var(--ghost);
    white-space: nowrap;
  }
  .hero-photo {
    position: absolute;
    left: 382px;
    top: 0;
    width: 228px;
    height: 446px;
    background: linear-gradient(180deg, #6b5a4e 0%, #b08466 45%, #3a302c 100%);
  }
  .brand {
    position: absolute;
    left: 27px;
    top: 30px;
  }
  .brand-mark {
    width: 70px;
    height: 70px;
    border: 3px solid var(--white);
    border-radius: 50%;
    margin-bottom: 24px;
  }
  .brand-name {
    font-family: "Oswald", sans-serif;
    font-weight: 600;
    font-size: 22px;
    letter-spacing: 0.5px;
    line-height: 1;
  }
  .brand-byline {
    font-family: "Oswald", sans-serif;
    font-weight: 400;
    font-size: 14px;
    letter-spacing: 0.5px;
    margin-top: 6px;
  }
  .offer {
    position: absolute;
    left: 26px;
    top: 222px;
    font-family: "Oswald", sans-serif;
    font-weight: 600;
    font-size: 50px;
    line-height: 62px;
    color: var(--olive);
    -webkit-text-stroke: 1px var(--olive-dark);
    text-shadow: 0 2px 3px rgba(0, 0, 0, 0.6);
  }
  .title-band {
    position: absolute;
    left: 0;
    top: 446px;
    width: 610px;
    height: 120px;
    background: linear-gradient(180deg, var(--blue-top) 0%, var(--blue-bottom) 100%);
    text-align: center;
    font-family: "Oswald", sans-serif;
    font-weight: 600;
    text-transform: uppercase;
    padding-top: 12px;
  }
  .venue {
    font-size: 46px;
    line-height: 54px;
  }
  .event-name {
    font-size: 32px;
    line-height: 40px;
  }
  .class-band {
    position: absolute;
    left: 0;
    top: 578px;
    width: 610px;
    height: 36px;
    background: var(--olive);
    text-align: center;
    font-family: "Oswald", sans-serif;
    font-weight: 500;
    font-size: 20px;
    line-height: 36px;
    text-transform: uppercase;
  }
  .schedule {
    position: absolute;
    right: 14px;
    top: 634px;
    text-align: right;
  }
  .schedule-title {
    font-family: "Oswald", sans-serif;
    font-weight: 500;
    font-size: 40px;
    line-height: 52px;
    text-transform: uppercase;
  }
  .schedule-list {
    list-style: none;
    font-size: 20px;
    line-height: 29.5px;
  }
  .schedule-list li::before { content: "\2022"; }
  .schedule-list strong { font-weight: 700; }
  .dates {
    position: absolute;
    left: 0;
    top: 836px;
    width: 610px;
    text-align: center;
    font-size: 20px;
  }
  .contact {
    position: absolute;
    left: 0;
    top: 874px;
    width: 610px;
    text-align: center;
    font-size: 14px;
    color: var(--lime-link);
  }
  .contact span + span { margin-left: 6px; }
</style>
</head>
<body>
  <main class="poster">
    <div class="brand-watermark" aria-hidden="true">VITA FORGE</div>

    <div class="hero-photo" role="img" aria-label="Photo of a fitness trainer in sportswear throwing a punch toward the viewer"></div>

    <header class="brand">
      <div class="brand-mark" aria-hidden="true"></div>
      <div class="brand-name">VITA FORGE</div>
      <div class="brand-byline">BY DALE WINTHAM</div>
    </header>

    <h2 class="offer">PLUS: 30 Minute<br>Private Training<br>Sessions</h2>

    <section class="title-band">
      <h1 class="venue">The Halcott Spires Gym</h1>
      <p class="event-name">Complimentary Fitness &amp; Wellness</p>
    </section>

    <p class="class-band">Complimentary Yoga, Pilates &amp; Interval Training Bootcamp Classes</p>

    <section class="schedule">
      <h3 class="schedule-title">Schedule:</h3>
      <ul class="schedule-list">
        <li><strong>Halcott Spires Gym</strong> 9:00am - 9:30am</li>
        <li><strong>Yoga</strong> 9:45am - 10:15am</li>
        <li><strong>Interval Training Bootcamp</strong> 11:45am -12:15pm</li>
        <li><strong>Pilates</strong> 9:00am - 12:00pm</li>
        <li><strong>Kids Karate Classes Also Available</strong></li>
      </ul>
    </section>

    <p class="dates">Saturday May 18th, 25th &amp; June 1st Time: 9:00am - 12:15pm</p>

    <p class="contact"><span>www.Vitaforge.tv</span><span>Info@vitaforge.tv</span></p>
  </main>
</body>
</html>
```